Corvane Paintless Dent Removal

Our company works on vehicles removing dents using a highly skilled trade which the metal is massaged out with special tools without disturbing the original paint, hence paintless dent removal. Besides keeping the paint and metal original its also very environmentally friendly since no paint or toxic fillers are used. Also we we are one of the most experienced companies in the business with 25 years

Target Market(s)

Retail Automobile consumers, Auto Dealerships and Auto Body Shops

Industry/Entity Type

Auto Repair

Contact Information for Business Card

Dale Hollister
PO Box 518 Brookmere, NY 11962
631-555-0148
corvanepdr@mailbox-example.com
website corvanepdr.example
youtube corvane paintless dent removal
25 years of experience removing Dents, Dings and Hail Damage

Font styles to use
Serif
Sans Serif

Colors

Designer to choose colors to be used in the design.

Requirements
Must have
• I do like things that are simple but classy and somewhat bold, also I like my logo so that should be somewhat important

```html
<!DOCTYPE html>
<html lang="en">
<head>
<meta charset="utf-8">
<title>Corvane Paintless Dent Removal – Business Card</title>
<link href="https://fonts.googleapis.com/css2?family=Roboto:wght@400;500;700;900&display=swap" rel="stylesheet">
<style>
  :root {
    --backdrop: #3b3b3d;
    --card: #27282a;
    --card-edge: #1e1f21;
    --navy: #13285a;
    --brand-blue: #1d5fb8;
    --lime: #7cc623;
    --white: #ffffff;
    --text-soft: #e4e4e4;
  }
  * { margin: 0; padding: 0; box-sizing: border-box; }
  html, body {
    width: 799px;
    height: 1200px;
    overflow: hidden;
    background: var(--backdrop);
    font-family: "Roboto", Arial, sans-serif;
  }
  .card {
    position: absolute;
    left: 80px;
    width: 640px;
    height: 366px;
    background: var(--card);
    border: 1px solid var(--card-edge);
    overflow: hidden;
    box-shadow: 0 10px 30px rgba(0,0,0,0.45);
  }
  .card--front { top: 150px; }
  .card--back { top: 640px; }

  .brand {
    position: absolute;
    display: flex;
    align-items: center;
    gap: 14px;
    color: var(--brand-blue);
    font-weight: 900;
    text-transform: uppercase;
    line-height: 1.05;
  }
  .brand__dot {
    flex: none;
    border-radius: 50%;
    background: var(--brand-blue);
  }
  .card--front .brand {
    left: 0; right: 0; top: 0; bottom: 0;
    justify-content: center;
  }
  .card--front .brand__dot { width: 46px; height: 46px; }
  .card--front .brand__name { font-size: 34px; letter-spacing: 1px; }
  .card--front .brand__tag { display: block; font-size: 17px; letter-spacing: 1.5px; }

  .card--back .brand { left: 42px; top: 92px; }
  .card--back .brand__dot { width: 34px; height: 34px; }
  .card--back .brand__name { font-size: 25px; letter-spacing: 0.5px; }
  .card--back .brand__tag { display: block; font-size: 12.5px; letter-spacing: 1px; }

  .wave { position: absolute; inset: 0; }

  .person {
    position: absolute;
    right: 38px;
    top: 128px;
    text-align: right;
    color: var(--white);
  }
  .person__name { font-size: 29px; font-weight: 700; }
  .person__title { font-size: 14px; font-weight: 400; margin-top: 2px; color: var(--text-soft); }

  .contact {
    position: absolute;
    left: 42px;
    top: 232px;
    list-style: none;
    color: var(--text-soft);
    font-size: 14px;
  }
  .contact li { display: flex; align-items: center; gap: 10px; height: 22px; }
  .contact svg { width: 13px; height: 13px; fill: none; stroke: var(--lime); stroke-width: 1.6; }

  .postal {
    position: absolute;
    right: 38px;
    bottom: 26px;
    text-align: right;
    color: var(--text-soft);
    font-size: 15px;
    line-height: 1.5;
  }
  .postal__channel { display: inline-flex; align-items: center; gap: 8px; }
  .postal__mark { width: 14px; height: 10px; background: #d62b2b; border-radius: 2px; }
</style>
</head>
<body>

<section class="card card--front" aria-label="Card front">
  <div class="brand">
    <span class="brand__dot"></span>
    <span class="brand__name">Corvane<span class="brand__tag">Paintless Dent Removal</span></span>
  </div>
</section>

<section class="card card--back" aria-label="Card back">
  <svg class="wave" viewBox="0 0 640 366" preserveAspectRatio="none" aria-hidden="true">
    <path d="M210 0 L640 0 L640 300 C560 292 520 250 470 190 C410 118 330 40 210 0 Z" fill="var(--navy)"/>
    <path d="M180 26 C320 40 410 110 470 180 C530 250 570 292 640 310" fill="none" stroke="var(--lime)" stroke-width="7"/>
    <path d="M240 12 C350 40 420 95 470 150" fill="none" stroke="var(--lime)" stroke-width="2.5"/>
    <path d="M205 0 C330 36 410 110 470 185 C525 252 565 290 640 302" fill="none" stroke="#1a1b1d" stroke-width="3"/>
  </svg>

  <div class="brand">
    <span class="brand__dot"></span>
    <span class="brand__name">Corvane<span class="brand__tag">Paintless Dent Removal</span></span>
  </div>

  <div class="person">
    <div class="person__name">Dale Hollister</div>
    <div class="person__title">Managing Director</div>
  </div>

  <ul class="contact">
    <li><svg viewBox="0 0 14 14"><path d="M3 1.5 L5.5 1.5 L6.5 4.5 L5 5.5 C5.8 7.3 6.7 8.2 8.5 9 L9.5 7.5 L12.5 8.5 L12.5 11 C12.5 12 11.5 12.7 10.5 12.5 C6 11.6 2.4 8 1.5 3.5 C1.3 2.5 2 1.5 3 1.5 Z"/></svg>631-555-0148</li>
    <li><svg viewBox="0 0 14 14"><rect x="1" y="3" width="12" height="8"/><path d="M1 3 L7 8 L13 3"/></svg>corvanepdr@mailbox-example.com</li>
    <li><svg viewBox="0 0 14 14"><circle cx="7" cy="7" r="5.8"/><path d="M1.2 7 H12.8 M7 1.2 C4.5 4 4.5 10 7 12.8 C9.5 10 9.5 4 7 1.2"/></svg>www.corvanepdr.example</li>
  </ul>

  <div class="postal">
    <span class="postal__channel"><span class="postal__mark"></span>/Dale Hollister</span><br>
    PO Box 518 Brookmere, NY 11962
  </div>
</section>

</body>
</html>
```